Telvo Website - endlich neu?!
Aufgabenstellung
Es geht um die Gestaltung der Startseite auf Basis unseres verwendeten Magento-Templates.
Außerdem um die Gestaltung von Visitenkarte und Briefkopf.

```html
<!DOCTYPE html>
<html lang="de">
<head>
<meta charset="utf-8">
<title>Telvo – Die Jackenerweiterung</title>
<link rel="stylesheet" href="https://fonts.googleapis.com/css2?family=Arimo:wght@400;700&family=Gochi+Hand&display=swap">
<style>
  :root {
    --ink: #1a1a1a;
    --text: #222222;
    --muted: #a8a8a8;
    --line: #bdbdbd;
    --panel: #f1f1f1;
    --accent: #e4202a;
    --lime: #d8e04a;
    --white: #ffffff;
    --photo-warm: #8a4a57;
    --photo-mid: #b9a9a0;
    --photo-light: #e7e2dc;
  }
  * { margin: 0; padding: 0; box-sizing: border-box; }
  html, body { width: 1200px; height: 805px; overflow: hidden; background: var(--white); }
  body { position: relative; font-family: "Arimo", Arial, sans-serif; color: var(--text); }

  .top-strip { position: absolute; left: 88px; top: 0; width: 1017px; height: 5px; background: var(--panel); }

  .language { position: absolute; left: 889px; top: 0; width: 216px; height: 42px; background: var(--panel);
    border-radius: 0 0 4px 4px; display: flex; align-items: center; padding-left: 23px; gap: 14px; }
  .language-label { font-size: 13px; color: var(--muted); margin-right: 6px; }
  .flag { width: 26px; height: 18px; border-radius: 4px; overflow: hidden; display: block; }

  .brand { position: absolute; left: 98px; top: 44px; }
  .brand-name { display: block; font-size: 66px; font-weight: 400; color: var(--ink); line-height: 1; }
  .tagline { display: block; margin-top: 10px; font-size: 15px; color: var(--muted); letter-spacing: 0.5px; }

  .main-nav { position: absolute; left: 88px; top: 163px; width: 1018px; height: 45px; border: 1px solid var(--line);
    border-radius: 4px; box-shadow: 0 1px 2px rgba(0,0,0,.15); display: flex; align-items: center; }
  .nav-list { list-style: none; display: flex; height: 24px; align-items: center; }
  .nav-item { height: 24px; display: flex; align-items: center; padding: 0 27px; border-right: 1px solid var(--line); font-size: 14.5px; color: var(--text); }
  .nav-item:first-child { padding-left: 32px; padding-right: 33px; }
  .nav-item.is-active span { font-weight: 700; font-size: 15px; color: #444; border-bottom: 2px solid var(--accent); padding-bottom: 1px; }
  .search { position: absolute; right: 10px; top: 8px; width: 205px; height: 27px; background: var(--panel); border-radius: 14px;
    display: flex; align-items: center; justify-content: space-between; padding: 0 9px 0 17px; font-size: 13px; color: var(--muted); }

  .hero { position: absolute; left: 89px; top: 225px; width: 1017px; height: 378px;
    background: radial-gradient(ellipse at 80% 25%, var(--photo-light) 0%, var(--photo-mid) 45%, transparent 70%),
                linear-gradient(100deg, var(--photo-warm) 0%, #c7a6aa 35%, #5b4a4c 62%, #cfc5bb 100%); }
  .hero-caption { position: absolute; right: 0; bottom: 0; width: 321px; height: 116px; background: rgba(110,110,110,.72);
    border-radius: 22px 22px 0 0; }
  .hero-caption svg { position: absolute; left: 0; top: 0; }
  .caption-line { position: absolute; font-family: "Gochi Hand", cursive; font-size: 31px; letter-spacing: 2px; line-height: 1; white-space: nowrap; }
  .caption-line.one { left: 28px; top: 26px; color: var(--white); }
  .caption-line.two { left: 77px; top: 64px; color: var(--lime); }

  .like-button { position: absolute; left: 89px; top: 603px; width: 99px; height: 24px; border: 1px solid #9a9a9a; background: #eeeeee;
    display: flex; align-items: center; gap: 5px; padding-left: 7px; font-size: 12px; font-weight: 700; color: #333; }
  .like-square { width: 11px; height: 11px; background: #777; }

  .site-footer { position: absolute; left: 88px; top: 698px; width: 1018px; height: 46px; border: 1px solid var(--line); border-radius: 4px;
    display: flex; align-items: center; justify-content: space-between; padding: 0 25px 0 29px; font-size: 12.5px; color: var(--text); }
  .footer-links .sep { margin: 0 11px; }
</style>
</head>
<body>
  <div class="top-strip"></div>

  <div class="language">
    <span class="language-label">Your Language:</span>
    <svg class="flag" viewBox="0 0 26 18" aria-label="Deutsch">
      <rect width="26" height="6" fill="#000"/><rect y="6" width="26" height="6" fill="#dd0000"/><rect y="12" width="26" height="6" fill="#ffce00"/>
    </svg>
    <svg class="flag" viewBox="0 0 26 18" aria-label="English">
      <rect width="26" height="18" fill="#012169"/>
      <path d="M0 0L26 18M26 0L0 18" stroke="#fff" stroke-width="4"/>
      <path d="M0 0L26 18M26 0L0 18" stroke="#c8102e" stroke-width="1.5"/>
      <path d="M13 0V18M0 9H26" stroke="#fff" stroke-width="6"/>
      <path d="M13 0V18M0 9H26" stroke="#c8102e" stroke-width="3"/>
    </svg>
  </div>

  <div class="brand">
    <span class="brand-name">Telvo</span>
    <span class="tagline">Die Jackenerweiterung</span>
  </div>

  <nav class="main-nav">
    <ul class="nav-list">
      <li class="nav-item is-active"><span>HOME</span></li>
      <li class="nav-item">Was ist Telvo</li>
      <li class="nav-item">Rund um Telvo</li>
      <li class="nav-item">Shop</li>
      <li class="nav-item">Händler</li>
    </ul>
    <div class="search">
      <span>Suche</span>
      <svg width="16" height="16" viewBox="0 0 16 16"><circle cx="8" cy="8" r="7" fill="none" stroke="#9a9a9a" stroke-width="1.2"/><path d="M6 4.5L11 8L6 11.5Z" fill="#9a9a9a"/></svg>
    </div>
  </nav>

  <div class="hero" role="img" aria-label="Foto: Baby mit gestreifter Mütze schläft warm eingepackt in der Jackenerweiterung auf dem Arm">
    <div class="hero-caption">
      <svg width="321" height="116" viewBox="0 0 321 116">
        <path d="M8 116V30Q8 10 28 10H292Q312 10 312 30V116" fill="none" stroke="#d8d8d8" stroke-width="3" stroke-dasharray="14 7"/>
      </svg>
      <span class="caption-line one">Wohlig warm</span>
      <span class="caption-line two">auf dem Arm!</span>
    </div>
  </div>

  <div class="like-button"><span class="like-square"></span>Gefällt mir</div>

  <footer class="site-footer">
    <div class="footer-links">Sitemap<span class="sep">I</span>Impressum<span class="sep">I</span>Kontakt</div>
    <div class="copyright">© 2011 Telvo</div>
  </footer>
</body>
</html>
```